Label/sheets for packaging/boxing

We need a label to go on our shipping boxes. Also a time to reorder label or card to put into boxes. We want to use this in different sizes. I want our logo, which we will provide to be used on all items.I would like a flag and eagle ( I will provide file) to be graduated screen tint in upper left or the left side and my company logo and information to be on top solid.....or any design that is better than this idea...I would like the label 4x2.5 inched landscape......I would like to use the file to print different size labels.
Really, the design can be anything using my logo........I'm open for design.
Also, a time to re-order card or label with logo and info, it can include a thank you for ordering from us................confidence, etc. I really want this to stand out and look great.
Updates

Project Deadline Extended
Reason: We are able to add more time to project. Thanks.

Target Market(s)

Business, City accounts.

Industry/Entity Type

Shipping

Requirements
Must have
• Name address contact information, web address....ect.

Eco friendly....
Professional

```html
<!DOCTYPE html>
<html lang="en">
<head>
<meta charset="utf-8">
<title>Harbor Lane Printing – Shipping Labels</title>
<link rel="stylesheet" href="https://fonts.googleapis.com/css2?family=Courier+Prime:wght@400;700&display=swap">
<style>
  :root {
    --kraft: #d4a979;
    --sheet: #ffffff;
    --paper: #f6f6f4;
    --navy: #1b3668;
    --maroon: #8e1044;
    --rule-navy: #3d5a8c;
    --rule-maroon: #a0365f;
    --ink: #222222;
    --photo-blue: #3a4a80;
    --photo-red: #b8323c;
    --photo-light: #e4e2e2;
    --eco-red: #b51e2c;
  }
  * { box-sizing: border-box; margin: 0; padding: 0; }
  html, body { width: 849px; height: 1200px; overflow: hidden; }
  body {
    background: var(--kraft);
    position: relative;
    font-family: "Courier Prime", "Courier New", monospace;
    color: var(--ink);
  }

  .label {
    position: absolute;
    background: var(--sheet);
    border-radius: 2.2em;
    padding: 0.9em;
    box-shadow: 0 2px 6px rgba(80, 50, 20, 0.25);
  }
  .label--sm { left: 270px; top: 41px;  width: 310px; height: 205px; font-size: 6.4px; }
  .label--md { left: 168px; top: 290px; width: 514px; height: 306px; font-size: 10.2px; }
  .label--lg { left: 67px;  top: 644px; width: 718px; height: 513px; font-size: 14.4px; }

  .label__face {
    position: relative;
    width: 100%;
    height: 100%;
    border-radius: 1.5em;
    overflow: hidden;
    background: var(--paper);
  }

  .label__photo {
    position: absolute;
    left: 0; top: 0; bottom: 0;
    width: 60%;
    background:
      linear-gradient(to right, rgba(246,246,244,0) 50%, var(--paper) 100%),
      linear-gradient(160deg, var(--photo-blue) 0%, var(--photo-light) 45%, var(--photo-red) 100%);
  }

  .label__eco {
    position: absolute;
    left: 0; bottom: 0;
    width: 6.5%;
    min-width: 3.4em;
    height: 13%;
    background: var(--eco-red);
    display: flex;
    align-items: center;
    justify-content: center;
  }
  .label__eco svg { width: 70%; height: auto; }

  .label__crayon {
    position: absolute;
    right: 0; top: 3%; bottom: 14%;
    width: 4.5%;
    background: linear-gradient(to bottom, #f4d21c 0%, #f39322 18%, #e8457f 36%, #c2409b 50%, #9b79c8 64%, #6b6fc4 76%, #2aa4c9 90%, #f6f6f4 100%);
    opacity: 0.85;
  }

  .brand {
    position: absolute;
    left: 58%;
    top: 5%;
    display: flex;
    align-items: center;
    gap: 0.6em;
  }
  .brand__mark {
    width: 2.6em;
    height: 2.6em;
    background: var(--maroon);
    flex: none;
  }
  .brand__name {
    font-weight: 700;
    font-size: 2em;
    line-height: 1.05;
    color: var(--navy);
  }

  .contact {
    position: absolute;
    left: 51%;
    top: 30%;
    width: 42%;
  }
  .contact__row {
    display: flex;
    align-items: flex-end;
    height: 1.95em;
  }
  .contact__key {
    flex: none;
    width: 4.6em;
    font-weight: 700;
    font-size: 0.95em;
    color: var(--navy);
  }
  .contact__key--short { width: 2.5em; }
  .contact__key--accent { color: var(--maroon); }
  .contact__val {
    flex: 1;
    min-width: 0;
    font-size: 1em;
    padding-left: 0.3em;
    border-bottom: 1px solid var(--rule-navy);
    white-space: nowrap;
  }
  .contact__val--accent { border-bottom-color: var(--rule-maroon); }

  .label__signline {
    position: absolute;
    left: 50%;
    right: 8%;
    bottom: 8%;
    border-bottom: 1px solid #555a66;
  }
</style>
</head>
<body>

  <article class="label label--sm">
    <div class="label__face">
      <div class="label__photo" role="img" aria-label="Waving American flag with a bald eagle portrait, fading into white"></div>
      <div class="label__eco">
        <svg viewBox="0 0 24 24" aria-hidden="true"><path d="M12 3l3 5h-2l-1 0-1 0H9zM4 17l3-5 1 1.8-1.5 2.5h5v2H5zM20 17l-3 5v-2h-4v-2h5l-1.2-2 1.7-1z" fill="#fff"/></svg>
      </div>
      <div class="label__crayon" role="img" aria-label="Colourful crayon scribbles along the edge"></div>
      <div class="brand"><span class="brand__mark"></span><span class="brand__name">Harbor Lane<br>Printing</span></div>
      <dl class="contact">
        <div class="contact__row"><dt class="contact__key">Name</dt><dd class="contact__val">Harbor Lane Printing</dd></div>
        <div class="contact__row"><dt class="contact__key">Address</dt><dd class="contact__val">2240 Mill Road</dd></div>
        <div class="contact__row"><dt class="contact__key"></dt><dd class="contact__val">Lodi, CA. 95240</dd></div>
        <div class="contact__row"><dt class="contact__key">Phone</dt><dd class="contact__val">(209) 555-01472</dd></div>
        <div class="contact__row"><dt class="contact__key">Fax</dt><dd class="contact__val">(209) 555-0193</dd></div>
        <div class="contact__row"><dt class="contact__key contact__key--accent">Email</dt><dd class="contact__val contact__val--accent">hlprint@mailbox.com</dd></div>
        <div class="contact__row"><dt class="contact__key contact__key--accent contact__key--short">Web</dt><dd class="contact__val">www.harborlaneprinting.com</dd></div>
      </dl>
      <div class="label__signline"></div>
    </div>
  </article>

  <article class="label label--md">
    <div class="label__face">
      <div class="label__photo" role="img" aria-label="Waving American flag with a bald eagle portrait, fading into white"></div>
      <div class="label__eco">
        <svg viewBox="0 0 24 24" aria-hidden="true"><path d="M12 3l3 5h-2l-1 0-1 0H9zM4 17l3-5 1 1.8-1.5 2.5h5v2H5zM20 17l-3 5v-2h-4v-2h5l-1.2-2 1.7-1z" fill="#fff"/></svg>
      </div>
      <div class="label__crayon" role="img" aria-label="Colourful crayon scribbles along the edge"></div>
      <div class="brand"><span class="brand__mark"></span><span class="brand__name">Harbor Lane<br>Printing</span></div>
      <dl class="contact">
        <div class="contact__row"><dt class="contact__key">Name</dt><dd class="contact__val">Harbor Lane Printing</dd></div>
        <div class="contact__row"><dt class="contact__key">Address</dt><dd class="contact__val">2240 Mill Road</dd></div>
        <div class="contact__row"><dt class="contact__key"></dt><dd class="contact__val">Lodi, CA. 95240</dd></div>
        <div class="contact__row"><dt class="contact__key">Phone</dt><dd class="contact__val">(209) 555-01472</dd></div>
        <div class="contact__row"><dt class="contact__key">Fax</dt><dd class="contact__val">(209) 555-0193</dd></div>
        <div class="contact__row"><dt class="contact__key contact__key--accent">Email</dt><dd class="contact__val contact__val--accent">hlprint@mailbox.com</dd></div>
        <div class="contact__row"><dt class="contact__key contact__key--accent contact__key--short">Web</dt><dd class="contact__val">www.harborlaneprinting.com</dd></div>
      </dl>
      <div class="label__signline"></div>
    </div>
  </article>

  <article class="label label--lg">
    <div class="label__face">
      <div class="label__photo" role="img" aria-label="Waving American flag with a bald eagle portrait, fading into white"></div>
      <div class="label__eco">
        <svg viewBox="0 0 24 24" aria-hidden="true"><path d="M12 3l3 5h-2l-1 0-1 0H9zM4 17l3-5 1 1.8-1.5 2.5h5v2H5zM20 17l-3 5v-2h-4v-2h5l-1.2-2 1.7-1z" fill="#fff"/></svg>
      </div>
      <div class="label__crayon" role="img" aria-label="Colourful crayon scribbles along the edge"></div>
      <div class="brand"><span class="brand__mark"></span><span class="brand__name">Harbor Lane<br>Printing</span></div>
      <dl class="contact">
        <div class="contact__row"><dt class="contact__key">Name</dt><dd class="contact__val">Harbor Lane Printing</dd></div>
        <div class="contact__row"><dt class="contact__key">Address</dt><dd class="contact__val">2240 Mill Road</dd></div>
        <div class="contact__row"><dt class="contact__key"></dt><dd class="contact__val">Lodi, CA. 95240</dd></div>
        <div class="contact__row"><dt class="contact__key">Phone</dt><dd class="contact__val">(209) 555-01472</dd></div>
        <div class="contact__row"><dt class="contact__key">Fax</dt><dd class="contact__val">(209) 555-0193</dd></div>
        <div class="contact__row"><dt class="contact__key contact__key--accent">Email</dt><dd class="contact__val contact__val--accent">hlprint@mailbox.com</dd></div>
        <div class="contact__row"><dt class="contact__key contact__key--accent contact__key--short">Web</dt><dd class="contact__val">www.harborlaneprinting.com</dd></div>
      </dl>
      <div class="label__signline"></div>
    </div>
  </article>

</body>
</html>
```